Business card design for holistic health care clinic

We need a double-sided business card design for our holistic health care clinic that integrates our logo design and also its color scheme. My business is called Valmira. It is an integrative medicine clinic. You have already done the logo for me. Please ensure an elegant and upscale design that is not cluttered, but still has all the necessary information (please see below for details).

Target Market(s)

Wellness, fitness, rehabilitation for educated, well-traveled open-minded clients who are focused on natural, organic, balanced and preventive healthcare and lifestyle.

Industry/Entity Type

Medical

Contact Information for Business Card

Modern, clean.

Number of Pages Required

1 page

Font styles to use
Serif
Sans Serif

Colors

Designer to choose colors to be used in the design.

Requirements
Must have
• Logo on one side, all other information on the other side.
• Other information should include:
• Tobias Wrenfeld - DOE, CPT, LMT
• 4100 East Marrow Drive
• Austin, TX 78119
• 512 555 0148
• 818 555 0192
• info@ValmiraHealth.example
• t.wrenfeld@ValmiraHealth.example
Nice to have
• Darker background on front - but not totally black - shaded/dark gray.

```html
<!DOCTYPE html>
<html lang="en">
<head>
<meta charset="utf-8">
<title>Valmira – Business Card</title>
<link href="https://fonts.googleapis.com/css2?family=Mulish:wght@400;600;700;800;900&display=swap" rel="stylesheet">
<style>
  :root {
    --backdrop: #c9c9c9;
    --card-dark-top: #3a3c3f;
    --card-dark-bottom: #222426;
    --brand-blue: #0a90d0;
    --card-blue: #0a93d1;
    --ink-dark: #2a2d31;
    --text-light: #ffffff;
  }
  * { margin: 0; padding: 0; box-sizing: border-box; }
  html, body {
    width: 1200px; height: 960px; overflow: hidden;
    background: var(--backdrop);
    font-family: "Mulish", Arial, sans-serif;
  }
  .canvas { position: relative; width: 1200px; height: 960px; }

  .card {
    position: absolute;
    width: 602px; height: 344px;
    border-radius: 22px;
    overflow: hidden;
    box-shadow: 2px 4px 8px rgba(0,0,0,0.25);
  }

  /* Front: contact side */
  .card-front {
    left: 302px; top: 116px;
    background: linear-gradient(180deg, var(--card-dark-top) 0%, var(--card-dark-bottom) 100%);
  }
  .front-wordmark {
    position: absolute; right: 44px; top: 62px;
    text-align: right; color: var(--brand-blue);
  }
  .front-wordmark .brand-name {
    display: block;
    font-size: 56px; font-weight: 800; line-height: 1;
    letter-spacing: 0.5px; text-transform: uppercase;
  }
  .front-wordmark .brand-descriptor {
    display: block; margin-top: 4px;
    font-size: 15px; font-weight: 700;
  }
  .holder {
    position: absolute; left: 38px; top: 184px;
    color: var(--brand-blue);
  }
  .holder-name {
    font-size: 20px; font-weight: 800; letter-spacing: 0.6px;
    text-transform: uppercase; line-height: 1;
  }
  .holder-credentials {
    margin-top: 4px; font-size: 12px; font-weight: 800; letter-spacing: 0.5px;
  }
  .address {
    position: absolute; right: 42px; top: 183px;
    text-align: right; color: var(--text-light);
    font-size: 14px; line-height: 17px; letter-spacing: 0.3px;
  }
  .contact-list {
    position: absolute; right: 44px; top: 226px;
    list-style: none; color: var(--text-light);
    font-size: 14px; letter-spacing: 0.3px;
  }
  .contact-list li {
    display: flex; justify-content: flex-end; align-items: center;
    height: 19.5px;
  }
  .contact-list svg { width: 13px; height: 13px; margin-left: 8px; fill: var(--brand-blue); }

  /* Back: brand side */
  .card-back {
    left: 299px; top: 500px;
    background: var(--card-blue);
  }
  .back-wordmark {
    position: absolute; left: 0; right: 0; top: 132px;
    text-align: center; color: var(--ink-dark);
  }
  .back-wordmark .brand-name {
    display: block;
    font-size: 80px; font-weight: 800; line-height: 1;
    letter-spacing: 1px; text-transform: uppercase;
  }
  .back-wordmark .brand-descriptor {
    display: block; margin-top: 2px;
    font-size: 19px; font-weight: 700;
  }
  .tagline {
    position: absolute; left: 0; right: 0; top: 280px;
    display: flex; justify-content: center; align-items: center;
    color: var(--ink-dark); font-size: 14px; letter-spacing: 0.4px;
  }
  .tagline::before, .tagline::after {
    content: ""; width: 60px; height: 1px; background: var(--ink-dark);
  }
  .tagline span { padding: 0 2px; }
</style>
</head>
<body>
<main class="canvas">

  <section class="card card-front" aria-label="Business card front">
    <div class="front-wordmark">
      <span class="brand-name">Valmira</span>
      <span class="brand-descriptor">Integrative Holistic Medicine</span>
    </div>

    <div class="holder">
      <p class="holder-name">Tobias Wrenfeld</p>
      <p class="holder-credentials">DOE, CPT, LMT</p>
    </div>

    <address class="address" style="font-style:normal">
      4100 East Marrow Drive<br>
      Austin, TX 78119
    </address>

    <ul class="contact-list">
      <li>512 555 0148
        <svg viewBox="0 0 24 24"><path d="M6.6 10.8a15.1 15.1 0 0 0 6.6 6.6l2.2-2.2c.3-.3.7-.4 1-.2 1.1.4 2.3.6 3.6.6.6 0 1 .4 1 1V20c0 .6-.4 1-1 1A17 17 0 0 1 3 4c0-.6.4-1 1-1h3.5c.6 0 1 .4 1 1 0 1.3.2 2.5.6 3.6.1.3 0 .7-.2 1z"/></svg>
      </li>
      <li style="margin-bottom:4px">818 555 0192
        <svg viewBox="0 0 24 24"><path d="M7 1h10a2 2 0 0 1 2 2v18a2 2 0 0 1-2 2H7a2 2 0 0 1-2-2V3a2 2 0 0 1 2-2zm0 3v15h10V4zm5 16.2a.9.9 0 1 0 0 1.8.9.9 0 0 0 0-1.8z"/></svg>
      </li>
      <li>t.wrenfeld@ValmiraHealth.example
        <svg viewBox="0 0 24 24"><path d="M2 5h20v14H2zm2 2v.5l8 5 8-5V7zm0 2.8V17h16V9.8l-8 5z"/></svg>
      </li>
      <li>www.ValmiraHealth.example
        <svg viewBox="0 0 24 24"><circle cx="12" cy="12" r="10"/><path d="M8 6c2 1 1 3 3 4s0 3 2 4M15 4c-1 2 1 3 3 3M16 16c1 1 0 3 1 4" stroke="#2a2c2f" stroke-width="1.6" fill="none"/></svg>
      </li>
    </ul>
  </section>

  <section class="card card-back" aria-label="Business card back">
    <div class="back-wordmark">
      <span class="brand-name">Valmira</span>
      <span class="brand-descriptor">Integrative Holistic Medicine</span>
    </div>
    <p class="tagline"><span>helping the body help itself</span></p>
  </section>

</main>
</body>
</html>
```